Help me make landing pages for my web application that are mobile friendly

I need to make 2 mobile friendly landing pages for an application. The 2 pages will be related. First I need a home page and then I need a working page. I do not want to change the color scheme or logos. Just layout and design.

```html
<!DOCTYPE html>
<html lang="en">
<head>
<meta charset="utf-8">
<title>ShiftCover – Mobile Screens</title>
<link href="https://fonts.googleapis.com/css2?family=Lato:wght@400;700;900&display=swap" rel="stylesheet">
<style>
:root{
  --stage:#d5d5d5;
  --white:#ffffff;
  --purple:#6b4fa8;
  --purple-dark:#5a3f96;
  --teal:#2aaad0;
  --panel:#f1f9fc;
  --panel-border:#e2f0f6;
  --ink:#1f1f2b;
  --muted:#555a66;
  --chip:#eeeef2;
  --green:#22b014;
  --red:#e01f1f;
  --field-border:#eef1f4;
}
*{box-sizing:border-box;margin:0;padding:0}
html,body{width:888px;height:1200px;overflow:hidden;background:var(--stage);font-family:"Lato",sans-serif;color:var(--ink)}
.canvas{width:1036px;height:1400px;transform:scale(0.857143);transform-origin:0 0;position:relative}
.phone{position:absolute;background:var(--white);overflow:hidden}
.phone-home{left:73px;top:70px;width:414px;height:1260px}
.phone-work{left:549px;top:70px;width:414px;height:1140px}
.brand{position:absolute;left:21px;top:18px;display:flex;align-items:center;gap:9px}
.brand-dot{width:26px;height:26px;border-radius:50%;background:var(--teal)}
.brand-name{font-size:25px;font-weight:700;color:var(--teal)}
.menu{position:absolute;right:20px;top:24px}
.tabs{position:absolute;left:21px;top:70px;display:flex;gap:12px;white-space:nowrap}
.tab{height:32px;border-radius:16px;padding:0 12px;display:flex;align-items:center;gap:6px;font-size:12px;background:var(--white);box-shadow:0 1px 4px rgba(0,0,0,.12)}
.tab.active{background:var(--purple);color:var(--white);font-size:14px;font-weight:700}
.panel{position:absolute;background:var(--panel);border:2px solid var(--panel-border);border-radius:10px}
.home-panel{left:19px;top:130px;width:376px;height:1090px}
.panel-title{position:absolute;left:18px;top:20px;font-size:18px;font-weight:700}
.card{position:absolute;left:19px;width:336px;height:143px;background:var(--white);border-radius:14px;box-shadow:0 1px 6px rgba(0,0,0,.06)}
.chip{position:absolute;left:38px;top:14px;background:var(--chip);border-radius:10px;padding:3px 12px;font-size:12px}
.avatar{position:absolute;left:37px;top:48px;width:45px;height:45px;border-radius:50%;background:linear-gradient(135deg,#9aa1ab,#5b6170)}
.avatar.initials{background:#c9cbd0;color:var(--white);font-size:13px;font-weight:700;display:flex;align-items:center;justify-content:center}
.tick{position:absolute;left:69px;top:80px;width:13px;height:13px;border-radius:50%;background:var(--white);display:flex;align-items:center;justify-content:center}
.who{position:absolute;left:93px;top:46px}
.who-name{font-size:14px;font-weight:700;color:var(--teal)}
.who-role{font-size:11px;color:var(--muted);margin-top:5px}
.meta{position:absolute;left:93px;top:88px;font-size:11px;color:var(--muted)}
.meta b{color:var(--ink);font-weight:700}
.meta.status{left:192px;display:flex;align-items:center;gap:4px}
.meta.slots{top:114px}
.badge{border-radius:9px;padding:2px 6px;color:var(--white);font-size:11px;font-weight:700}
.badge.complete{background:var(--teal)}
.badge.active{background:var(--green)}
.badge.cancelled{background:var(--red)}
.nav{position:absolute;left:0;bottom:0;width:414px;height:68px;background:var(--purple);display:flex;justify-content:space-around;align-items:center;color:var(--white)}
.nav-item{display:flex;flex-direction:column;align-items:center;gap:3px;font-size:11px;font-weight:700}
.nav-item.home{font-size:14px}
.nav-icon{width:26px;height:26px;display:flex;align-items:center;justify-content:center}
.nav-item.home .nav-icon{background:var(--white);border-radius:50%}
.work-panel{left:19px;top:68px;width:376px;height:1020px}
.form-title{position:absolute;left:18px;top:20px;font-size:18px;font-weight:700}
.row{position:absolute;left:20px;right:16px;display:flex;align-items:flex-start}
.label{width:96px;font-size:14px;font-weight:700;line-height:17px;padding-top:5px}
.field{flex:1;min-height:28px;background:var(--white);border:1px solid var(--field-border);border-radius:12px;font-size:11px;padding:7px 18px;color:var(--muted);position:relative}
.field.tall{height:56px;line-height:16px}
.field.time{display:flex;justify-content:space-between;align-items:center}
.pill{height:26px;border-radius:13px;padding:0 20px;display:flex;align-items:center;font-size:12px;font-weight:700;color:var(--white)}
.mini-btn{height:26px;border:1px solid var(--field-border);background:var(--white);border-radius:13px;padding:0 12px;display:inline-flex;align-items:center;gap:6px;font-size:11px;color:var(--muted)}
.outline-btn{position:absolute;right:8px;height:18px;border:1px solid var(--teal);border-radius:9px;padding:0 7px;font-size:10px;color:var(--teal);display:flex;align-items:center;gap:4px}
.note{position:absolute;left:15px;top:64px;background:var(--panel);border-radius:12px;padding:5px 9px;font-size:11px}
.actions{position:absolute;left:103px;top:983px;display:flex;gap:13px}
.btn{height:32px;border-radius:16px;padding:0 20px;display:flex;align-items:center;gap:8px;font-size:15px}
.btn.save{background:var(--purple);color:var(--white);font-weight:700}
.btn.close{background:#e8e9ef;color:var(--ink)}
</style>
</head>
<body>
<div class="canvas">

  <section class="phone phone-home">
    <div class="brand"><span class="brand-dot"></span><span class="brand-name">ShiftCover</span></div>
    <svg class="menu" width="22" height="18" viewBox="0 0 22 18"><path d="M1 2h20M5 9h16M1 16h20" stroke="#6b4fa8" stroke-width="2.4" stroke-linecap="round"/></svg>
    <div class="tabs">
      <div class="tab active">My Assignments
        <svg width="20" height="14" viewBox="0 0 20 14"><path d="M2 11l5-6 3 4 6-8M13 1h4v4" stroke="#fff" stroke-width="2" fill="none"/></svg></div>
      <div class="tab">Available Openings
        <svg width="20" height="14" viewBox="0 0 20 14"><path d="M2 11l5-6 3 4 6-8M13 1h4v4" stroke="#6b4fa8" stroke-width="2" fill="none"/></svg></div>
      <div class="tab">My Assignments</div>
    </div>

    <div class="panel home-panel">
      <h2 class="panel-title">My Assignments</h2>

      <article class="card" style="top:56px">
        <span class="chip">Subbing For:</span>
        <div class="avatar" role="img" aria-label="Profile photo of Nora Whitfield"></div>
        <span class="tick"><svg width="9" height="9" viewBox="0 0 9 9"><path d="M1.5 4.5l2 2 4-4" stroke="#22b014" stroke-width="1.5" fill="none"/></svg></span>
        <div class="who"><div class="who-name">Nora Whitfield</div><div class="who-role">Teacher</div></div>
        <div class="meta"><b>Location:</b> MGES</div>
        <div class="meta status"><b>Status:</b><span class="badge complete">Complete</span></div>
        <div class="meta slots"><b>Time Slots:</b> 09/02 - 09/02 (1h 0m)</div>
      </article>

      <article class="card" style="top:221px">
        <span class="chip">Subbing For:</span>
        <div class="avatar" role="img" aria-label="Profile photo for extra duty"></div>
        <span class="tick"><svg width="9" height="9" viewBox="0 0 9 9"><path d="M1.5 4.5l2 2 4-4" stroke="#22b014" stroke-width="1.5" fill="none"/></svg></span>
        <div class="who"><div class="who-name">Extra duty</div><div class="who-role">Teacher</div></div>
        <div class="meta"><b>Location:</b> MGES</div>
        <div class="meta status"><b>Status:</b><span class="badge complete">Complete</span></div>
        <div class="meta slots"><b>Time Slots:</b> 09/02 - 09/02 (1h 0m)</div>
      </article>

      <article class="card" style="top:386px">
        <span class="chip">Subbing For:</span>
        <div class="avatar initials">OH</div>
        <span class="tick"><svg width="9" height="9" viewBox="0 0 9 9"><path d="M1.5 4.5l2 2 4-4" stroke="#22b014" stroke-width="1.5" fill="none"/></svg></span>
        <div class="who"><div class="who-name">Owen Harlow</div><div class="who-role">Teacher</div></div>
        <div class="meta"><b>Location:</b> MGES</div>
        <div class="meta status"><b>Status:</b><span class="badge complete">Complete</span></div>
        <div class="meta slots"><b>Time Slots:</b> 09/02 - 09/02 (1h 0m)</div>
      </article>

      <article class="card" style="top:550px">
        <span class="chip">Subbing For:</span>
        <div class="avatar" role="img" aria-label="Profile photo of Felix Brandt"></div>
        <span class="tick"><svg width="9" height="9" viewBox="0 0 9 9"><path d="M1.5 4.5l2 2 4-4" stroke="#22b014" stroke-width="1.5" fill="none"/></svg></span>
        <div class="who"><div class="who-name">Felix Brandt</div><div class="who-role">Administrator</div></div>
        <div class="meta"><b>Location:</b> MGES</div>
        <div class="meta status"><b>Status:</b><span class="badge active">Active</span></div>
        <div class="meta slots"><b>Time Slots:</b> 09/02 - 09/02 (1h 0m)</div>
      </article>

      <article class="card" style="top:715px">
        <span class="chip">Subbing For:</span>
        <div class="avatar" role="img" aria-label="Profile photo of Ravi Ellison"></div>
        <span class="tick"><svg width="9" height="9" viewBox="0 0 9 9"><path d="M1.5 4.5l2 2 4-4" stroke="#22b014" stroke-width="1.5" fill="none"/></svg></span>
        <div class="who"><div class="who-name">Ravi Ellison</div><div class="who-role">Teacher</div></div>
        <div class="meta"><b>Location:</b> MGES</div>
        <div class="meta status"><b>Status:</b><span class="badge cancelled">Cancelled</span></div>
        <div class="meta slots"><b>Time Slots:</b> 09/02 - 09/02 (1h 0m)</div>
      </article>

      <article class="card" style="top:880px">
        <span class="chip">Subbing For:</span>
        <div class="avatar" role="img" aria-label="Profile photo of Colin Prescott"></div>
        <span class="tick"><svg width="9" height="9" viewBox="0 0 9 9"><path d="M1.5 4.5l2 2 4-4" stroke="#22b014" stroke-width="1.5" fill="none"/></svg></span>
        <div class="who"><div class="who-name">Colin Prescott</div><div class="who-role">Teacher</div></div>
        <div class="meta"><b>Location:</b> MGES</div>
        <div class="meta status"><b>Status:</b><span class="badge active">Active</span></div>
        <div class="meta slots"><b>Time Slots:</b> 09/02 - 09/02 (1h 0m)</div>
      </article>
    </div>

    <nav class="nav">
      <div class="nav-item home"><span class="nav-icon"><svg width="14" height="14" viewBox="0 0 14 14"><path d="M1 7l6-5 6 5M3 6v6h8V6" fill="#6b4fa8"/></svg></span>Home</div>
      <div class="nav-item"><span class="nav-icon"><svg width="24" height="24" viewBox="0 0 24 24"><circle cx="10" cy="10" r="7" stroke="#fff" stroke-width="2" fill="none"/><path d="M15 15l6 6" stroke="#fff" stroke-width="2"/></svg></span>Available Opening</div>
      <div class="nav-item"><span class="nav-icon"><svg width="20" height="20" viewBox="0 0 20 20"><rect x="3" y="3" width="14" height="14" rx="2" stroke="#fff" stroke-width="2" fill="none"/><path d="M6 8h8M6 12h6" stroke="#fff" stroke-width="2"/></svg></span>Assignments</div>
      <div class="nav-item"><span class="nav-icon"><svg width="22" height="22" viewBox="0 0 22 22"><circle cx="11" cy="11" r="9" stroke="#fff" stroke-width="2" fill="none"/><circle cx="11" cy="9" r="3" fill="#fff"/><path d="M6 17c2-3 8-3 10 0" stroke="#fff" stroke-width="2" fill="none"/></svg></span>Support</div>
    </nav>
  </section>

  <section class="phone phone-work">
    <div class="brand"><span class="brand-dot"></span><span class="brand-name">ShiftCover</span></div>
    <svg class="menu" width="22" height="18" viewBox="0 0 22 18"><path d="M1 2h20M5 9h16M1 16h20" stroke="#6b4fa8" stroke-width="2.4" stroke-linecap="round"/></svg>

    <div class="panel work-panel">
      <h2 class="form-title">Opening Information</h2>
      <div class="row" style="top:55px"><span class="label">Summary</span><span class="field">Testing-test</span></div>
      <div class="row" style="top:98px"><span class="label">Location</span><span class="field">Maple Grove Elementary School</span></div>
      <div class="row" style="top:142px"><span class="label">Type</span><span class="field">Vacancy</span></div>
      <div class="row" style="top:185px"><span class="label">Regular Staff</span><span class="field">lb Owen Harlow</span></div>
      <div class="row" style="top:228px"><span class="label" style="width:148px">Assignment Category</span><span class="field">Teacher</span></div>
      <div class="row" style="top:272px"><span class="label">Department</span><span class="field">Testing</span></div>
      <div class="row" style="top:315px"><span class="label">Description</span><span class="field tall">asdf<br>sffsd</span></div>
      <div class="row" style="top:385px"><span class="label">Comments</span>
        <span class="field" style="height:112px;padding-top:12px;line-height:16px">Write a comment or upload a<br>file...
          <span class="outline-btn" style="top:12px">&#10148; Post</span>
          <span class="outline-btn" style="top:38px">&#8599; Upload</span>
          <span class="note">No comments or files uploaded</span>
        </span></div>
      <div class="row" style="top:515px"><span class="label">Additional Details</span><span class="field tall">Parking Spot</span></div>
      <div class="row" style="top:585px"><span class="label">Time Slots</span>
        <span style="display:flex;gap:8px"><span class="mini-btn">&#9900; Accept</span><span class="mini-btn">&#9645; Withdraw</span></span></div>
      <div class="row" style="top:630px"><span class="label">From</span><span class="field time">2:30 PM <span>&#9719;</span></span></div>
      <div class="row" style="top:675px"><span class="label">To</span><span class="field time">4:00 PM <span>&#9719;</span></span></div>
      <div class="row" style="top:717px"><span class="label" style="width:143px">Current Assignment</span><span class="pill" style="background:var(--teal);flex:1">No Assignment</span></div>
      <div class="row" style="top:761px"><span class="label" style="width:62px">Status</span><span class="pill" style="background:var(--green);padding:0 24px">Active</span></div>
      <div class="row" style="top:810px"><span class="label">From</span><span class="field time">2:30 PM <span>&#9719;</span></span></div>
      <div class="row" style="top:855px"><span class="label">To</span><span class="field time">4:00 PM <span>&#9719;</span></span></div>
      <div class="actions" style="top:913px">
        <span class="btn save"><svg width="18" height="16" viewBox="0 0 18 16"><path d="M9 1v9M5 6l4 4 4-4M2 10v5h14v-5" stroke="#fff" stroke-width="1.8" fill="none"/></svg>Save</span>
        <span class="btn close">&#10005;&nbsp; Close</span>
      </div>
    </div>

    <nav class="nav">
      <div class="nav-item home"><span class="nav-icon"><svg width="14" height="14" viewBox="0 0 14 14"><path d="M1 7l6-5 6 5M3 6v6h8V6" fill="#6b4fa8"/></svg></span>Home</div>
      <div class="nav-item"><span class="nav-icon"><svg width="24" height="24" viewBox="0 0 24 24"><circle cx="10" cy="10" r="7" stroke="#fff" stroke-width="2" fill="none"/><path d="M15 15l6 6" stroke="#fff" stroke-width="2"/></svg></span>Available Opening</div>
      <div class="nav-item"><span class="nav-icon"><svg width="20" height="20" viewBox="0 0 20 20"><rect x="3" y="3" width="14" height="14" rx="2" stroke="#fff" stroke-width="2" fill="none"/><path d="M6 8h8M6 12h6" stroke="#fff" stroke-width="2"/></svg></span>Assignments</div>
      <div class="nav-item"><span class="nav-icon"><svg width="22" height="22" viewBox="0 0 22 22"><circle cx="11" cy="11" r="9" stroke="#fff" stroke-width="2" fill="none"/><circle cx="11" cy="9" r="3" fill="#fff"/><path d="M6 17c2-3 8-3 10 0" stroke="#fff" stroke-width="2" fill="none"/></svg></span>Support</div>
    </nav>
  </section>

</div>
</body>
</html>
```